Business Card Design Project

I require a business card with the following information on them for various different people;
name
m:
f:
e:
I have a logo already and will attached that. We are in the construction industry. I require something clean and simple but eye catching at the same time. You can use another colour with our logo if you like and you can style the logo as well if you wish. I am open.
Also it needs to be front and back design.
Industry/Entity Type
Construction
Requirements
Must have
- Logo, name, mobile, fax and email address.
Front and back design

```html
<!DOCTYPE html>
<html lang="en">
<head>
<meta charset="utf-8">
<title>Stonebridge Works – Business Card</title>
<link rel="stylesheet" href="https://fonts.googleapis.com/css2?family=Arimo:wght@400&family=Roboto+Condensed:wght@400&display=swap">
<style>
  :root {
    --paper: #ffffff;
    --crop: #1a1a1a;
    --card: #070909;
    --glow: #2e3030;
    --green: #8dc63f;
    --green-bright: #6cc04a;
    --green-deep: #1f4a26;
    --grey-band: #858585;
    --text: #ffffff;
  }
  * { margin: 0; padding: 0; box-sizing: border-box; }
  html, body { width: 1200px; height: 884px; overflow: hidden; background: var(--paper); }
  .sheet { position: relative; width: 1200px; height: 884px; }
  .crop { position: absolute; background: var(--crop); }
  .crop--v { width: 1px; height: 120px; }
  .crop--h { height: 1px; width: 120px; }

  .card {
    position: absolute; left: 181px; top: 181px; width: 835px; height: 522px;
    border-radius: 42px; overflow: hidden;
    background: radial-gradient(ellipse 60% 45% at 50% 0%, var(--glow) 0%, var(--card) 75%);
  }
  .brand {
    position: absolute; left: 0; right: 0; top: 150px;
    display: flex; justify-content: center; align-items: center; gap: 14px;
  }
  .brand__mark { width: 34px; height: 34px; background: var(--green-bright); }
  .brand__name {
    font-family: "Arimo", Arial, sans-serif; font-weight: 400;
    font-size: 54px; color: var(--green-bright); letter-spacing: -0.5px;
  }
  .person {
    position: absolute; left: 60px; top: 259px;
    font-family: "Arimo", Arial, sans-serif; font-weight: 400;
    font-size: 40px; line-height: 40px; color: var(--green);
  }
  .person__rule {
    position: absolute; left: 19px; top: 303px; width: 484px; height: 2px;
    background: linear-gradient(90deg, transparent 0%, var(--green) 25%, #4a6b2a 85%, transparent 100%);
  }
  .contacts { position: absolute; left: 58px; top: 311px; list-style: none; }
  .contacts li {
    display: flex; align-items: center; gap: 12px; height: 41px;
    font-family: "Roboto Condensed", "Arial Narrow", sans-serif; font-weight: 400;
    font-size: 26px; line-height: 1; color: var(--text);
  }
  .contacts li:nth-child(3) { height: 35px; }
  .contacts svg { width: 22px; height: 22px; flex: none; }
  .bands { position: absolute; left: 0; top: 0; width: 835px; height: 522px; }
</style>
</head>
<body>
<div class="sheet">
  <span class="crop crop--v" style="left:181px;top:0"></span>
  <span class="crop crop--v" style="left:1018px;top:0"></span>
  <span class="crop crop--v" style="left:181px;top:764px"></span>
  <span class="crop crop--v" style="left:1018px;top:764px"></span>
  <span class="crop crop--h" style="left:0;top:181px"></span>
  <span class="crop crop--h" style="left:0;top:703px"></span>
  <span class="crop crop--h" style="left:1080px;top:181px"></span>
  <span class="crop crop--h" style="left:1080px;top:703px"></span>

  <section class="card">
    <svg class="bands" viewBox="0 0 835 522" aria-hidden="true">
      <defs>
        <linearGradient id="deepBand" x1="0" x2="1">
          <stop offset="0" stop-color="#1f4a26"/>
          <stop offset="0.6" stop-color="#1a3a1e"/>
          <stop offset="1" stop-color="#000000"/>
        </linearGradient>
      </defs>
      <polygon points="425,416 835,416 835,431 405,431" fill="var(--grey-band)"/>
      <rect x="0" y="432" width="835" height="34" fill="url(#deepBand)"/>
      <polygon points="88,466 835,466 835,479 102,479" fill="var(--green)"/>
    </svg>

    <div class="brand">
      <span class="brand__mark"></span>
      <span class="brand__name">Stonebridge Works</span>
    </div>

    <h1 class="person">Martin Hale</h1>
    <div class="person__rule"></div>

    <ul class="contacts">
      <li>
        <svg viewBox="0 0 22 22" aria-hidden="true"><rect x="6" y="4" width="10" height="16" rx="2.5" fill="#8dc63f"/><rect x="8" y="1" width="2" height="4" fill="#8dc63f"/><rect x="8.5" y="7" width="5" height="4" fill="#070909"/></svg>
        0400 555 182
      </li>
      <li>
        <svg viewBox="0 0 22 22" aria-hidden="true"><rect x="2" y="8" width="18" height="11" rx="1.5" fill="none" stroke="#8dc63f" stroke-width="1.6"/><rect x="6" y="2" width="10" height="6" fill="none" stroke="#8dc63f" stroke-width="1.6"/><rect x="9" y="11" width="8" height="5" fill="#8dc63f"/><rect x="4" y="11" width="3" height="6" fill="#8dc63f"/></svg>
        03 9555 0147
      </li>
      <li>
        <svg viewBox="0 0 22 22" aria-hidden="true"><rect x="2" y="5" width="18" height="12" fill="none" stroke="#8dc63f" stroke-width="1.6"/><path d="M2 5 L11 12 L20 5 M2 17 L9 10.5 M20 17 L13 10.5" fill="none" stroke="#8dc63f" stroke-width="1.6"/></svg>
        martin@sbworks.com.au
      </li>
    </ul>
  </section>
</div>
</body>
</html>
```